FernPath....... a dash of Glow

I need a web design for a new business based in London that will be mobile (offered at homes, parks or a local cafe ect) called FernPath. I offer Life Coaching/Counselling sessions, Personal training, Massage and Sports Massage. Sessions range from an hour to half and hour. My aim is to help people along their journey to help give them gain clarity of where there going, helping them to towards their goals, so that can experience bliss. My website should represent a place people can come to release their stress and worries so that they leave feeling lighter, clearer and happier. I would like my website to reflect someone feeling ALIVE. I would also like a logo design for FernPath with a sentence underneath or near saying A dash of Glow.

Target Market(s)

middle class people

Industry/Entity Type

Business

Coding

Coded - Design and coding required

Number of Pages Required

4 page

Requirements
Must have
• 1st page About us
• 2nd page Services
• 3rd page Prices
• 4th page contact details
Nice to have
• mixture of cultures in images

```html
<!DOCTYPE html>
<html lang="en">
<head>
<meta charset="utf-8">
<title>FernPath — A dash of Glow</title>
<link href="https://fonts.googleapis.com/css2?family=Raleway:wght@400;500;700;800&family=Open+Sans:wght@400;600&display=swap" rel="stylesheet">
<style>
  :root{
    --teal:#14c4b2;
    --teal-dark:#0ea597;
    --teal-deep:#0b9487;
    --orange:#f7681a;
    --orange-light:#ff8a1e;
    --yellow:#fdb812;
    --yellow-light:#fdd02a;
    --ink:#2f2f2f;
    --text:#555;
    --muted:#777;
    --footer:#e3e3e3;
    --white:#fff;
  }
  *{margin:0;padding:0;box-sizing:border-box}
  html,body{width:912px;height:1200px;overflow:hidden;background:var(--white)}
  body{position:relative;font-family:"Open Sans",Arial,sans-serif;color:var(--text)}
  .abs{position:absolute}

  /* header */
  .brand{left:143px;top:24px}
  .brand-name{font-family:"Raleway",Arial,sans-serif;font-weight:400;font-size:35px;color:var(--teal);letter-spacing:-.5px;line-height:1}
  .brand-tag{font-family:"Raleway",Arial,sans-serif;font-size:13.5px;color:var(--orange);margin-top:5px}
  .call{right:139px;top:45px;text-align:right}
  .call-label{font-family:"Raleway",Arial,sans-serif;font-size:9.5px;color:var(--teal-dark);font-weight:500;letter-spacing:.3px}
  .call-row{display:flex;align-items:center;gap:7px;margin-top:2px}
  .call-number{font-family:"Open Sans",Arial,sans-serif;font-size:15px;color:var(--ink);letter-spacing:.3px}

  /* nav */
  .nav{left:0;top:89px;width:912px;height:35px;background:linear-gradient(var(--teal),var(--teal-dark))}
  .nav ul{list-style:none;display:flex;position:absolute;left:138px;top:0;height:35px}
  .nav li{font-family:"Raleway",Arial,sans-serif;font-weight:500;font-size:11.5px;color:var(--white);height:35px;line-height:35px;text-align:center;border-right:1px solid rgba(255,255,255,.35)}
  .nav li:last-child,.nav li.active{border-right:none}
  .nav li.active{background:var(--teal-deep)}

  /* hero */
  .hero{left:46px;top:124px;width:765px;height:351px;background:
    radial-gradient(ellipse at 70% 20%,#f3f2f0 0%,rgba(243,242,240,0) 60%),
    radial-gradient(ellipse at 40% 35%,#e7c9b3 0%,rgba(231,201,179,0) 30%),
    radial-gradient(ellipse at 42% 55%,#8fa9c8 0%,rgba(143,169,200,0) 25%),
    radial-gradient(ellipse at 82% 62%,#2e3f5e 0%,rgba(46,63,94,0) 22%),
    linear-gradient(180deg,#eeeeec 0%,#e4e2df 60%,#f6f6f6 100%)}
  .hero-title{left:133px;top:258px;font-family:"Raleway",Arial,sans-serif;font-weight:800;font-size:30px;color:var(--ink);letter-spacing:1px}
  .hero-sub{left:134px;top:300px;font-family:"Raleway",Arial,sans-serif;font-size:21px;color:var(--orange);letter-spacing:.3px}
  .hero-dots{left:137px;top:338px;display:flex;gap:3px}
  .dot{width:13px;height:13px;border-radius:50%;background:var(--teal)}
  .dot.current{background:none;border:2.5px solid var(--orange)}

  /* service cards */
  .card{top:472px;width:206px;height:142px}
  .card svg.shape{position:absolute;left:0;top:0}
  .card-badge{position:absolute;left:59px;top:-46px;width:88px;height:88px;border-radius:50%;border:3px solid var(--white);display:flex;align-items:center;justify-content:center}
  .card h3{position:absolute;left:0;width:100%;top:50px;text-align:center;font-family:"Raleway",Arial,sans-serif;font-weight:400;font-size:15.5px;color:var(--white)}
  .card p{position:absolute;left:20px;width:166px;top:74px;text-align:center;font-size:8px;line-height:12px;color:var(--white)}
  .card-training .card-badge{background:var(--orange)}
  .card-massage .card-badge{background:var(--teal)}
  .card-coaching .card-badge{background:var(--yellow)}

  /* about */
  .about{left:25px;top:628px;width:887px;height:218px;background:linear-gradient(180deg,#fff 0%,#f7f7f7 70%,#efefef 100%)}
  .about h2{left:138px;top:644px;font-family:"Raleway",Arial,sans-serif;font-weight:400;font-size:21px;color:var(--ink)}
  .about-lead{left:138px;top:682px;width:400px;font-size:8.8px;line-height:16.5px;color:var(--ink)}
  .about-body{left:138px;top:722px;width:415px;font-size:7.4px;line-height:16.3px;color:var(--muted)}
  .about-photo{left:593px;top:625px;width:180px;height:180px;border-radius:50%;border:2px solid #fff;box-shadow:0 0 0 1px #ddd;background:radial-gradient(circle at 45% 40%,#9a9a9a 0%,#5a5a5a 45%,#1d1d1d 100%)}

  /* feature columns */
  .col-title{top:874px;font-family:"Raleway",Arial,sans-serif;font-weight:400;font-size:16.5px}
  .t-orange{color:var(--orange)}
  .t-teal{color:var(--teal)}
  .t-ink{color:var(--ink)}
  .col-photo{top:903px;width:200px;height:79px}
  .photo-mission{left:134px;background:linear-gradient(90deg,#6b4a34 0%,#c99a78 40%,#e9d7c8 75%,#f4ede6 100%)}
  .photo-goals{left:576px;width:200px;height:78px;top:902px;background:linear-gradient(90deg,#3a3f46 0%,#9fa6ae 30%,#f1f1f1 55%,#d8c7b6 80%,#4a4f57 100%)}
  .video{left:355px;top:901px;width:200px;height:151px;background:linear-gradient(180deg,#1b1b1b 0%,#b98c6e 35%,#d9b395 55%,#2a2a2a 80%,#111 100%)}
  .video-bar{position:absolute;left:0;bottom:0;width:200px;height:15px;background:#1c1c1c}
  .col-text{top:988px;width:190px;font-size:7.4px;line-height:13.6px;color:var(--text)}
  .btn{height:22px;width:80px;font-family:"Open Sans",Arial,sans-serif;font-size:8.3px;color:var(--white);text-align:center;line-height:22px;border-radius:2px}
  .btn-orange{left:135px;top:1037px;background:linear-gradient(var(--orange-light),var(--orange))}
  .btn-teal{left:580px;top:1036px;background:linear-gradient(#3fd6c5,var(--teal-dark))}

  /* footer */
  .footer{left:0;top:1110px;width:912px;height:90px;background:var(--footer)}
  .footer-links{left:134px;top:1136px;font-family:"Raleway",Arial,sans-serif;font-weight:500;font-size:10.5px;color:var(--ink);word-spacing:1px}
  .footer-copy{left:134px;top:1159px;font-size:8px;color:var(--ink)}
  .social{left:668px;top:1138px;display:flex;gap:3px}
  .social span{width:24px;height:24px;border-radius:50%;border:1.5px solid #222;display:block}
</style>
</head>
<body>

<header>
  <div class="brand abs">
    <div class="brand-name">FernPath</div>
    <div class="brand-tag">A dash of Glow</div>
  </div>
  <div class="call abs">
    <div class="call-label">CALL ME AT</div>
    <div class="call-row">
      <svg width="21" height="21" viewBox="0 0 22 22" aria-hidden="true">
        <circle cx="11" cy="11" r="9.8" fill="none" stroke="var(--orange)" stroke-width="1.6"/>
        <path d="M7.6 6.2c.5-.4 1.1-.3 1.4.2l1 1.6c.3.5.2 1-.2 1.3l-.6.5c.5 1.2 1.5 2.3 2.8 2.9l.5-.6c.3-.4.9-.5 1.3-.2l1.6 1c.5.3.6.9.2 1.4l-.6.7c-.6.6-1.5.8-2.3.5-2.8-1.1-4.9-3.2-6-6-.3-.8-.1-1.7.5-2.3z" fill="var(--orange)"/>
      </svg>
      <span class="call-number">685.555.0182</span>
    </div>
  </div>
</header>

<nav class="nav abs">
  <ul>
    <li class="active" style="width:76px">HOME</li>
    <li style="width:94px">ABOUT US</li>
    <li style="width:89px">SERVICES</li>
    <li style="width:100px">OUR MISSION</li>
    <li style="width:108px">TESTIMONIAL</li>
    <li style="width:83px">CONSULT</li>
    <li style="width:84px">CONTACT</li>
  </ul>
</nav>

<section>
  <div class="hero abs" role="img" aria-label="Photo of a smiling woman doing sit-ups with a personal trainer holding her feet in a bright studio"></div>
  <h1 class="hero-title abs">PERSONAL TRAINER</h1>
  <div class="hero-sub abs">A DASH OF GLOW</div>
  <div class="hero-dots abs"><span class="dot current"></span><span class="dot"></span><span class="dot"></span><span class="dot"></span></div>
</section>

<section class="services">
  <div class="card card-training abs" style="left:136px">
    <svg class="shape" width="206" height="142" viewBox="0 0 206 142" aria-hidden="true">
      <defs><linearGradient id="gOrange" x1="0" y1="0" x2="0" y2="1"><stop offset="0" stop-color="#ff8d1f"/><stop offset="1" stop-color="#f9560c"/></linearGradient></defs>
      <path d="M0 0H206V136Q103 142 0 130Z" fill="url(#gOrange)"/>
    </svg>
    <div class="card-badge">
      <svg width="46" height="48" viewBox="0 0 46 48" aria-hidden="true">
        <rect x="18" y="1" width="10" height="5" rx="1" fill="#fff"/>
        <rect x="21" y="5" width="4" height="5" fill="#fff"/>
        <circle cx="23" cy="28" r="18" fill="none" stroke="#fff" stroke-width="3"/>
        <path d="M23 28V14A14 14 0 1 1 13 18Z" fill="#fff"/>
        <path d="M36 10l4 4" stroke="#fff" stroke-width="3" stroke-linecap="round"/>
      </svg>
    </div>
    <h3>Personal Training</h3>
    <p>Fresh sessions at home, in the park or a local cafe, shaped around your own pace</p>
  </div>

  <div class="card card-massage abs" style="left:354px">
    <svg class="shape" width="206" height="142" viewBox="0 0 206 142" aria-hidden="true">
      <defs><linearGradient id="gTeal" x1="0" y1="0" x2="0" y2="1"><stop offset="0" stop-color="#19cbb9"/><stop offset="1" stop-color="#0da896"/></linearGradient></defs>
      <path d="M0 0H206V130Q103 146 0 130Z" fill="url(#gTeal)"/>
    </svg>
    <div class="card-badge">
      <svg width="48" height="44" viewBox="0 0 48 44" aria-hidden="true" fill="none" stroke="#fff" stroke-width="2.4" stroke-linecap="round" stroke-linejoin="round">
        <path d="M24 38S6 27 6 15a9 9 0 0 1 18-3 9 9 0 0 1 18 3c0 12-18 23-18 23z"/>
        <path d="M2 42h44"/>
      </svg>
    </div>
    <h3>Sports Massage</h3>
    <p>Ease tight muscles and let go of stress so you leave feeling lighter and clearer</p>
  </div>

  <div class="card card-coaching abs" style="left:571px">
    <svg class="shape" width="206" height="142" viewBox="0 0 206 142" aria-hidden="true">
      <defs><linearGradient id="gYellow" x1="0" y1="0" x2="0" y2="1"><stop offset="0" stop-color="#fdd22b"/><stop offset="1" stop-color="#fca812"/></linearGradient></defs>
      <path d="M0 0H206V130Q103 140 0 136Z" fill="url(#gYellow)"/>
    </svg>
    <div class="card-badge">
      <svg width="46" height="44" viewBox="0 0 46 44" aria-hidden="true" fill="none" stroke="#fff" stroke-width="2.6" stroke-linecap="round" stroke-linejoin="round">
        <path d="M4 40l12-14 8 8 16-22"/>
        <path d="M30 12h10v10"/>
        <rect x="30" y="28" width="12" height="12" fill="#fff"/>
      </svg>
    </div>
    <h3>Life Coaching</h3>
    <p>Gain clarity on where you are heading and take calm, steady steps toward your goals</p>
  </div>
</section>

<section>
  <div class="about abs"></div>
  <div class="about">
    <h2 class="abs">ABOUT FERNPATH</h2>
    <p class="about-lead abs">A mobile wellbeing service across London, bringing coaching, training and massage to the places where you feel most at ease</p>
    <p class="about-body abs">Every session runs from half an hour to a full hour and meets you where you are, whether that is your living room, a quiet green park or a corner table in your favourite cafe. The aim is simple: release the worries you carry, build strength in body and mind, and find a clear path to the goals that matter to you most.</p>
  </div>
  <div class="about-photo abs" role="img" aria-label="Black and white photo of hands giving a back massage"></div>
</section>

<section>
  <h3 class="col-title t-orange abs" style="left:135px">Our Mission</h3>
  <div class="col-photo photo-mission abs" role="img" aria-label="Photo of a man relaxing during a shoulder massage"></div>
  <p class="col-text abs" style="left:138px">We help you slow down, breathe and reconnect so every week brings more energy and calm</p>
  <div class="btn btn-orange abs">READ MORE</div>

  <h3 class="col-title t-teal abs" style="left:355px">Watch Our Video</h3>
  <div class="video abs" role="img" aria-label="Video still of a leg massage on a treatment table">
    <svg class="video-bar" width="200" height="15" viewBox="0 0 200 15" aria-hidden="true">
      <rect width="200" height="15" fill="#1c1c1c"/>
      <path d="M6 4l6 3.5-6 3.5z" fill="#fff"/>
      <rect x="16" y="6" width="140" height="3" rx="1.5" fill="#ddd"/>
      <rect x="16" y="6" width="54" height="3" rx="1.5" fill="#4a90d9"/>
      <path d="M185 5.5h2l3-2.5v9l-3-2.5h-2z" fill="#fff"/>
    </svg>
  </div>

  <h3 class="col-title t-ink abs" style="left:578px">Help to Achive Gols</h3>
  <div class="col-photo photo-goals abs" role="img" aria-label="Photo of two smiling trainers standing in a gym"></div>
  <p class="col-text abs" style="left:581px">Set clear targets, track your progress and celebrate each win with support at every single step</p>
  <div class="btn btn-teal abs">READ MORE</div>
</section>

<footer>
  <div class="footer abs"></div>
  <div class="footer-links abs">HOME &nbsp;|&nbsp; ABOUT US &nbsp;|&nbsp; SERVICES &nbsp;|&nbsp; OUR MISSION &nbsp;|&nbsp; TESTIMONIAL &nbsp;|&nbsp; CONSULT &nbsp;|&nbsp; CONTACT</div>
  <div class="footer-copy abs">© 2015 Company Name &nbsp;All right reserved &nbsp;Term of Use</div>
  <div class="social abs" aria-label="Social links"><span></span><span></span><span></span><span></span></div>
</footer>

</body>
</html>
```